VOMRA Pty Ltd Business Card

Looking for a simple yet eye-catching double-sided business card design using my company logo on one side and contact details on the other.

Target Market(s)

Government

Industry/Entity Type

Communication Systems Engineering

Contact Information for Business Card

VOMRA Pty Ltd

Requirements
Nice to have
• Would be great to have a QR code so details can be scanned into contacts

```html
<!DOCTYPE html>
<html lang="en">
<head>
<meta charset="utf-8">
<title>VOMRA Pty Ltd Business Card</title>
<link href="https://fonts.googleapis.com/css2?family=Open+Sans:wght@400;600;700&display=swap" rel="stylesheet">
<style>
  :root {
    --slate: #37414a;
    --paper: #ffffff;
    --ink: #1f2428;
    --backdrop: #e6e7e9;
    --rule: #2a2f33;
  }
  * { box-sizing: border-box; margin: 0; padding: 0; }
  html, body {
    width: 1200px; height: 780px; overflow: hidden;
    background: var(--backdrop);
    font-family: "Open Sans", Arial, sans-serif;
  }
  .sheet {
    width: 1200px; height: 780px;
    display: flex; flex-direction: column; align-items: center; justify-content: center;
    gap: 40px;
  }
  .card {
    width: 600px; height: 343px; position: relative; overflow: hidden;
    box-shadow: 0 6px 18px rgba(0,0,0,.18);
  }
  .card--back { background: var(--slate); display: flex; align-items: center; justify-content: center; }
  .card--front { background: var(--paper); color: var(--ink); }

  .wordmark { display: flex; align-items: center; gap: 16px; font-weight: 700; letter-spacing: 4px; }
  .wordmark__dot { border-radius: 50%; flex: none; }
  .card--back .wordmark { color: var(--paper); font-size: 64px; }
  .card--back .wordmark__dot { width: 58px; height: 58px; background: var(--paper); }

  .card--front .wordmark {
    position: absolute; top: 38px; left: 50%; transform: translateX(-50%);
    color: var(--slate); font-size: 50px;
  }
  .card--front .wordmark__dot { width: 44px; height: 44px; background: var(--slate); }

  .holder {
    position: absolute; top: 150px; right: 318px; text-align: right;
  }
  .holder__name { font-size: 28px; font-weight: 700; color: var(--slate); line-height: 1.15; }
  .holder__role { font-size: 16px; font-weight: 400; color: var(--ink); }

  .divider {
    position: absolute; left: 300px; top: 140px; width: 1px; height: 100px; background: var(--rule);
  }

  .contacts {
    position: absolute; left: 322px; top: 146px; list-style: none;
    font-size: 16px; line-height: 1.55;
  }
  .contacts li { display: flex; align-items: center; gap: 10px; }
  .contacts svg { width: 15px; height: 15px; flex: none; }

  .address-band {
    position: absolute; left: 0; right: 0; bottom: 34px; height: 36px;
    background: var(--slate); color: var(--paper);
    display: flex; align-items: center; justify-content: center;
    font-size: 16px; letter-spacing: .3px;
  }
</style>
</head>
<body>
<main class="sheet">
  <section class="card card--back" aria-label="Card back">
    <div class="wordmark"><span class="wordmark__dot"></span><span>VOMRA</span></div>
  </section>

  <section class="card card--front" aria-label="Card front">
    <div class="wordmark"><span class="wordmark__dot"></span><span>VOMRA</span></div>

    <div class="holder">
      <p class="holder__name">Jordan Whitley</p>
      <p class="holder__role">Co-Founder</p>
    </div>

    <span class="divider"></span>

    <ul class="contacts">
      <li>
        <svg viewBox="0 0 16 16" aria-hidden="true"><circle cx="8" cy="8" r="8" fill="#37414a"/><path d="M5.2 4.2l1.6-.4.8 2-1 .8a5 5 0 0 0 2.8 2.8l.8-1 2 .8-.4 1.6c-3.6.4-7-3-6.6-6.6z" fill="#fff"/></svg>
        <span>(555) 013-4827</span>
      </li>
      <li>
        <svg viewBox="0 0 16 16" aria-hidden="true"><circle cx="8" cy="8" r="8" fill="#37414a"/><circle cx="8" cy="8" r="5" fill="none" stroke="#fff" stroke-width="1"/><path d="M3 8h10M8 3c-2 2.8-2 7.2 0 10M8 3c2 2.8 2 7.2 0 10" fill="none" stroke="#fff" stroke-width="1"/></svg>
        <span>www.vomra.com.au</span>
      </li>
      <li>
        <svg viewBox="0 0 16 16" aria-hidden="true"><circle cx="8" cy="8" r="8" fill="#37414a"/><rect x="3.5" y="5" width="9" height="6.5" fill="none" stroke="#fff" stroke-width="1"/><path d="M3.5 5l4.5 4 4.5-4" fill="none" stroke="#fff" stroke-width="1"/></svg>
        <span>admin@vomra.com.au</span>
      </li>
    </ul>

    <div class="address-band">42-44 Harlow Street Redfield NSW 2099 Australia</div>
  </section>
</main>
</body>
</html>
```